Tarrowby Consulting needs a Business Catalogue

We are looking at creating a business catalogue that is used to introduce ourselves and our business as well as the services we offer. We are an HR business that offers assistance with recruitment and selection and all services involved in that area. We don't offer specific products and don't have prices advertised. it would be good to start with an introduction to the business and our history, some staff bios then a framework to discuss business scenarios where we can help. I would prefer white as the main colour on the front/back page with the colours of the logo (attached) to be used throughout the catalogue along with images and other visual improvements. A mall amount of colour should be used throughout and don't want solid colour pages. Prefer what pages that are broken up by coloured designs, images, diagrams heading etc. A 12-page catalogue with different designs I can move around as needed would be good.

Target Market(s)

Education, government, large business with administration staff

Font styles to use
Sans Serif

Requirements
Must have
• Logo colour scheme
• Images, diagrams, tables etc
• Start with company introduction (history, three staff profiles, company values etc)
• Main section will be the description of services and processes offered.
Nice to have
• A range of different visuals to choose from including designs for tables, paragraphs, diagrams, space for photos and other visual elements.

```html
<!DOCTYPE html>
<html lang="en">
<head>
<meta charset="utf-8">
<title>Tarrowby Consulting – Catalogue Covers</title>
<link href="https://fonts.googleapis.com/css2?family=Lato:wght@400;700&family=Montserrat:wght@600;700&display=swap" rel="stylesheet">
<style>
  :root {
    --backdrop: #e4e4e4;
    --paper: #ffffff;
    --brand-blue: #2196d3;
    --brand-blue-light: #4bb7e6;
    --brand-blue-deep: #1a86c4;
    --ink: #3a3d42;
    --link-blue: #1e8fcf;
    --city-light: #a9cde6;
    --city-mid: #4f8fb8;
    --city-deep: #1f5a80;
    --office-sky: #c9d8e6;
    --office-warm: #d8c2a6;
    --office-desk: #9fb2c2;
  }
  * { box-sizing: border-box; margin: 0; padding: 0; }
  html, body {
    width: 1200px; height: 824px; overflow: hidden;
    background: var(--backdrop);
  }
  .spread {
    position: absolute; left: 34px; top: 12px;
    width: 1132px; height: 800px;
    display: flex;
    box-shadow: 0 6px 24px rgba(0,0,0,0.12);
  }
  .page {
    position: relative; width: 566px; height: 800px;
    background: var(--paper); overflow: hidden;
  }
  .page--back { border-right: 1px solid #ececec; }

  .brand-mark {
    position: absolute; display: flex; align-items: center; gap: 10px;
    font-family: "Montserrat", sans-serif; font-weight: 600;
    font-size: 15px; line-height: 1.15; letter-spacing: 1px; color: var(--ink);
    text-transform: uppercase;
  }
  .brand-mark__square { width: 24px; height: 24px; background: var(--ink); flex: none; }
  .brand-mark__name { display: flex; flex-direction: column; }
  .page--back .brand-mark { left: 56px; top: 196px; }
  .page--front .brand-mark { left: 300px; top: 124px; }

  .photo { position: absolute; }
  .photo--skyline {
    left: 250px; top: 150px; width: 316px; height: 500px;
    background: linear-gradient(170deg, var(--city-light) 0%, var(--city-mid) 45%, var(--city-deep) 100%);
  }
  .spine-panel {
    position: absolute; left: 430px; top: 250px; width: 136px; height: 280px;
    background: var(--brand-blue-light); opacity: 0.85;
  }
  .spine-panel--lower {
    left: 470px; top: 530px; width: 96px; height: 110px;
    background: var(--brand-blue); opacity: 0.9;
  }

  .contact {
    position: absolute; left: 56px; top: 690px;
    font-family: "Lato", sans-serif; font-style: normal; font-size: 14px; line-height: 1.35;
    color: var(--link-blue);
  }

  .front-panel {
    position: absolute; left: 0; top: 220px; width: 250px; height: 400px;
    background: linear-gradient(180deg, var(--brand-blue-light) 0%, var(--brand-blue) 100%);
  }
  .title-box {
    position: absolute; left: 24px; top: 110px; width: 226px; height: 110px;
    background: var(--brand-blue-deep);
    display: flex; flex-direction: column; justify-content: center; padding-left: 22px;
    font-family: "Montserrat", sans-serif; font-weight: 700; color: var(--paper);
  }
  .title-box__name { font-size: 28px; letter-spacing: 0.5px; }
  .title-box__sub { font-size: 11px; letter-spacing: 6px; margin-top: 4px; }

  .photo--office {
    left: 150px; top: 280px; width: 390px; height: 230px;
    background: linear-gradient(180deg, var(--office-sky) 0%, var(--office-warm) 62%, var(--office-desk) 100%);
  }
  .web-address {
    position: absolute; right: 26px; top: 610px;
    font-family: "Lato", sans-serif; font-size: 14px; color: var(--link-blue);
  }
</style>
</head>
<body>
  <div class="spread">
    <section class="page page--back">
      <div class="brand-mark"><span class="brand-mark__square"></span><span class="brand-mark__name"><span>Tarrowby</span><span>Consulting</span></span></div>
      <div class="photo photo--skyline" role="img" aria-label="Photograph of a blue-toned city skyline of tall towers"></div>
      <div class="spine-panel"></div>
      <div class="spine-panel spine-panel--lower"></div>
      <address class="contact">
        Call: 123 456 7890<br>
        info@tarrowbyhr.com.au<br>
        www.tarrowbyhr.com.au
      </address>
    </section>

    <section class="page page--front">
      <div class="front-panel"></div>
      <div class="title-box">
        <span class="title-box__name">TARROWBY</span>
        <span class="title-box__sub">CONSULTING</span>
      </div>
      <div class="brand-mark"><span class="brand-mark__square"></span><span class="brand-mark__name"><span>Tarrowby</span><span>Consulting</span></span></div>
      <div class="photo photo--office" role="img" aria-label="Photograph of an office desk with laptop by tall windows overlooking a city"></div>
      <p class="web-address">www.tarrowbyhr.com.au</p>
    </section>
  </div>
</body>
</html>
```